Looking for someone to design a business card for my plumbing business Quandor Plumbing Solutions I want the background also to be black, must attract clients. If possible I want the front to be the logo and the back to show maybe the details.

Target Market(s)

Clients

Industry/Entity Type

Plumbing maintenance

Contact Information for Business Card

Name: Felix, Contact: 0461 539 207, Email: quandorplumbingsolutions@mailbrook.example, Licence number 728093K

Font styles to use
Other font styles liked:
• as per logo maybe?

Colors

Designer to choose colors to be used in the design.

Requirements
Nice to have
• stating the service I provide, emergency plumbing, plumbing maintenance, drainage maintenance, block sewer and stormwater, camera and locating.

```html
<!DOCTYPE html>
<html lang="en">
<head>
<meta charset="utf-8">
<title>Quandor Plumbing Solutions – Business Card</title>
<link href="https://fonts.googleapis.com/css2?family=Montserrat:wght@400;500;700;800&display=swap" rel="stylesheet">
<style>
  :root {
    --backdrop-light: #e6e5e3;
    --backdrop-dark: #b9b8b5;
    --card: #1f1f1f;
    --accent: #4a8fd6;
    --text: #ffffff;
    --mark-muted: #3a3a3a;
  }
  * { box-sizing: border-box; margin: 0; padding: 0; }
  html, body { width: 1200px; height: 801px; overflow: hidden; }
  body {
    background: radial-gradient(ellipse at 40% 20%, var(--backdrop-light), var(--backdrop-dark));
    font-family: "Montserrat", sans-serif;
    display: flex; align-items: center; justify-content: center; gap: 56px;
  }
  .card {
    width: 520px; height: 297px;
    background: var(--card);
    border-bottom: 4px solid var(--accent);
    border-left: 2px solid var(--accent);
    position: relative;
    box-shadow: 0 18px 30px rgba(0,0,0,.25);
    color: var(--text);
  }
  /* details side */
  .card--details { padding: 30px 30px 24px 34px; }
  .brand {
    display: flex; align-items: center; gap: 10px;
    font-weight: 700; font-size: 15px; letter-spacing: .5px; color: var(--accent);
    text-transform: uppercase;
  }
  .brand__dot { width: 14px; height: 14px; border-radius: 50%; background: var(--accent); }
  .identity-row { display: flex; align-items: center; margin-top: 42px; }
  .person { width: 176px; }
  .person__name { font-weight: 800; font-size: 26px; color: var(--accent); letter-spacing: 1px; line-height: 1; }
  .person__role, .person__licence { font-size: 12.5px; margin-top: 5px; }
  .divider { width: 1.5px; height: 66px; background: var(--accent); margin: 0 16px 0 6px; }
  .contacts { list-style: none; font-size: 11px; line-height: 1.9; }
  .contacts li { display: flex; align-items: center; gap: 7px; white-space: nowrap; }
  .contacts svg { width: 10px; height: 10px; flex: none; }
  .services {
    position: absolute; left: 34px; right: 24px; bottom: 24px;
    font-size: 11.5px; line-height: 1.7;
  }
  .services .sep { color: var(--accent); margin: 0 5px; }
  /* logo side */
  .card--logo { display: flex; align-items: center; justify-content: center; gap: 14px; }
  .mark__dot { width: 30px; height: 30px; border-radius: 50%; background: var(--mark-muted); }
  .mark__name {
    font-weight: 800; font-size: 26px; color: var(--mark-muted);
    text-transform: uppercase; letter-spacing: 1px; line-height: 1.1; width: 300px;
  }
</style>
</head>
<body>
  <section class="card card--details">
    <div class="brand"><span class="brand__dot"></span>Quandor Plumbing Solutions</div>

    <div class="identity-row">
      <div class="person">
        <div class="person__name">FELIX</div>
        <div class="person__role">Founder &amp; CEO</div>
        <div class="person__licence">Licence number 728093K</div>
      </div>
      <div class="divider"></div>
      <ul class="contacts">
        <li>
          <svg viewBox="0 0 10 10" aria-hidden="true"><path d="M2 0.5 L3.6 0.5 L4.2 3 L3 3.8 Q4 6 6.2 7 L7 5.8 L9.5 6.4 L9.5 8 Q9.5 9.5 8 9.5 Q0.5 9 0.5 2 Q0.5 0.5 2 0.5Z" fill="var(--accent)"/></svg>
          0461 539 207
        </li>
        <li>
          <svg viewBox="0 0 10 10" aria-hidden="true"><rect x="0.5" y="2" width="9" height="6.5" fill="var(--accent)"/><path d="M0.5 2 L5 5.8 L9.5 2" stroke="var(--card)" stroke-width="1" fill="none"/></svg>
          quandorplumbingsolutions@mailbrook.example
        </li>
        <li>
          <svg viewBox="0 0 10 10" aria-hidden="true"><circle cx="5" cy="5" r="4.5" fill="var(--accent)"/></svg>
          @QuandorPlumbingSolutions
        </li>
      </ul>
    </div>

    <p class="services">
      Emergency plumbing<span class="sep">•</span>Plumbing maintenance<span class="sep">•</span>Drainage maintenance<br>
      Block sewer and stormwater<span class="sep">•</span>Camera and locating
    </p>
  </section>

  <section class="card card--logo">
    <span class="mark__dot"></span>
    <span class="mark__name">Quandor Plumbing Solutions</span>
  </section>
</body>
</html>
```